Puffy Clouds Cotton Candy

Looking for a logo design and business cards to help a 13 year old entrepreneur promote her cotton candy business.
Contact Information for Business Card
Name, Phone & Email
Colors
E54698
E96AAD
F1A4CE
F9D9EA
FCEFF6
A7469A
B969AE
D3A5CF
EDDBEB
F8F0F9
6B429C
8869AF
B7A5CE
E3DAEB
F3F0F8
Requirements
Must have
- A fun feel that is appropriate for a teenage girl selling cotton candy

```html
<!DOCTYPE html>
<html lang="en">
<head>
<meta charset="utf-8">
<title>Puffy Clouds Cotton Candy – Business Card</title>
<link href="https://fonts.googleapis.com/css2?family=Poppins:wght@400;600;700&display=swap" rel="stylesheet">
<style>
  :root {
    --pink: #E54698;
    --pink-soft: #E96AAD;
    --orchid: #A7469A;
    --purple: #6B429C;
    --purple-soft: #8869AF;
    --ink: #2b2b2b;
    --white: #ffffff;
    --backdrop: #d2d2d4;
  }
  * { margin: 0; padding: 0; box-sizing: border-box; }
  html, body {
    width: 1200px; height: 900px; overflow: hidden;
    background: var(--backdrop);
    font-family: "Poppins", sans-serif;
  }
  .canvas {
    position: relative; width: 1200px; height: 900px;
  }
  .card {
    position: absolute;
    width: 640px; height: 366px;
    border-radius: 34px;
    box-shadow: 0 10px 24px rgba(0,0,0,0.22);
    overflow: hidden;
  }
  /* Front */
  .card-front {
    left: 150px; top: 48px;
    background: linear-gradient(30deg, var(--pink) 0%, var(--orchid) 55%, var(--purple) 100%);
    display: flex; align-items: center; justify-content: center;
  }
  .front-brand {
    display: flex; align-items: center; gap: 22px; color: var(--white);
  }
  .brand-dot {
    width: 74px; height: 74px; border-radius: 50%;
    border: 5px solid var(--white);
    flex: none;
  }
  .brand-name {
    font-weight: 700; line-height: 1.05; font-size: 40px;
  }
  .brand-name span { display: block; }
  /* Back */
  .card-back {
    left: 410px; top: 470px;
    background: var(--white);
    padding: 60px 60px;
  }
  .back-brand {
    display: flex; align-items: center; gap: 22px;
    color: var(--pink);
  }
  .back-brand .brand-dot {
    width: 90px; height: 90px; border: none; background: var(--pink);
  }
  .back-brand .brand-name { font-size: 36px; }
  .person { margin-top: 42px; }
  .person-name {
    color: var(--pink); font-weight: 700; font-size: 30px; line-height: 1.1;
  }
  .person-title {
    color: var(--purple); font-weight: 400; font-size: 20px;
  }
  .contact { margin-top: 16px; list-style: none; }
  .contact li {
    display: flex; align-items: center; gap: 10px;
    color: var(--ink); font-size: 18px; line-height: 1.6;
  }
  .contact svg { width: 20px; height: 20px; flex: none; }
</style>
</head>
<body>
<main class="canvas">
  <section class="card card-front" aria-label="Business card front">
    <div class="front-brand">
      <div class="brand-dot"></div>
      <div class="brand-name"><span>Puffy Clouds</span><span>Cotton Candy</span></div>
    </div>
  </section>

  <section class="card card-back" aria-label="Business card back">
    <div class="back-brand">
      <div class="brand-dot"></div>
      <div class="brand-name"><span>Puffy Clouds</span><span>Cotton Candy</span></div>
    </div>
    <div class="person">
      <p class="person-name">Maya Collins</p>
      <p class="person-title">Managing Director</p>
    </div>
    <ul class="contact">
      <li>
        <svg viewBox="0 0 24 24" aria-hidden="true"><path fill="#E54698" d="M6.6 10.8a15.1 15.1 0 0 0 6.6 6.6l2.2-2.2a1 1 0 0 1 1-.25 11.4 11.4 0 0 0 3.6.57 1 1 0 0 1 1 1V20a1 1 0 0 1-1 1A17 17 0 0 1 3 4a1 1 0 0 1 1-1h3.5a1 1 0 0 1 1 1c0 1.25.2 2.45.57 3.6a1 1 0 0 1-.25 1z"/></svg>
        044-555 010 203
      </li>
      <li>
        <svg viewBox="0 0 24 24" aria-hidden="true"><path fill="#E54698" d="M2 5h20v14H2zm2 2v.5l8 5 8-5V7zm0 2.8V17h16V9.8l-8 5z"/></svg>
        hello@puffyclouds.com
      </li>
    </ul>
  </section>
</main>
</body>
</html>
```